Dog grooming business card
This is a business card for m dog grooming business like it say above.
In the priorities box below I will have the text that I want on the card.

Industry/Entity Type

Business

Colors

Designer to choose colors to be used in the design.

Requirements
Must have
• My logo and the insurance stamp must be on the card.

Text it must have :

Professional grooming services
Email: lunabrisk@mailvale.net
Text or call 1 705 318 6052
TWF certified/member
Pet first aid certified
Next appointment ___________________________________
Nice to have
• Greens to match my logo

```html
<!DOCTYPE html>
<html lang="en">
<head>
<meta charset="UTF-8">
<title>Luna Brisk – Grooming Business Card</title>
<link href="https://fonts.googleapis.com/css2?family=Lobster&family=Arimo:wght@400&display=swap" rel="stylesheet">
<style>
  :root {
    --bg: #e6e8ec;
    --card: #ffffff;
    --green: #8cc63f;
    --ink: #1e1e1e;
    --badge-edge: #3a7fd0;
    --badge-fill: #eef5fd;
    --shadow: rgba(30, 35, 50, 0.18);
  }
  * { margin: 0; padding: 0; box-sizing: border-box; }
  html, body {
    width: 1200px; height: 960px; overflow: hidden;
    background: var(--bg);
  }
  .canvas {
    width: 1200px; height: 960px;
    display: flex; flex-direction: column;
    align-items: center; justify-content: center; gap: 60px;
  }
  .card {
    width: 640px; height: 366px;
    background: var(--card);
    border-radius: 16px;
    box-shadow: 0 10px 30px var(--shadow);
    position: relative;
  }
  /* Front */
  .card-front {
    display: flex; align-items: center; justify-content: center; gap: 18px;
  }
  .brand-dot {
    width: 54px; height: 54px; border-radius: 50%;
    background: var(--green);
  }
  .brand-name {
    font-family: 'Lobster', cursive;
    font-size: 64px; color: var(--green);
    line-height: 1;
  }
  /* Back */
  .card-back {
    padding: 40px 60px 34px;
    display: flex; flex-direction: column; align-items: center;
    font-family: 'Arimo', Arial, sans-serif;
  }
  .tagline {
    font-family: 'Lobster', cursive;
    font-size: 38px; color: var(--green);
    line-height: 1.1;
  }
  .credentials {
    margin-top: 14px; text-align: center;
    font-size: 17px; color: var(--ink); line-height: 1.25;
  }
  .insurance-stamp {
    margin-top: 10px;
    width: 82px; height: 36px;
    border: 2px solid var(--badge-edge);
    border-radius: 6px;
    background: var(--badge-fill);
  }
  .appointment-label {
    margin-top: 12px;
    font-size: 18px; color: var(--green);
  }
  .appointment-line {
    width: 440px; height: 0;
    border-bottom: 2px dotted var(--ink);
    margin-top: 26px;
  }
  .contact {
    margin-top: auto;
    font-size: 17px; color: var(--ink);
  }
  .contact .label { color: var(--green); }
</style>
</head>
<body>
<main class="canvas">
  <section class="card card-front" aria-label="Card front">
    <span class="brand-dot"></span>
    <span class="brand-name">Luna Brisk</span>
  </section>

  <section class="card card-back" aria-label="Card back">
    <h1 class="tagline">Professional grooming services</h1>
    <p class="credentials">TWF certified/member<br>Pet first aid certified</p>
    <div class="insurance-stamp" role="img" aria-label="Insurance stamp"></div>
    <p class="appointment-label">Next appointment</p>
    <div class="appointment-line"></div>
    <div class="appointment-line"></div>
    <p class="contact">
      <span class="label">Email</span> lunabrisk@mailvale.net /
      <span class="label">Text</span> or <span class="label">Call</span> 1 705 318 6052
    </p>
  </section>
</main>
</body>
</html>
```